Corlani Vaginal Suppositories eCommerce Website Design

We are designing an ecommerce website for a new company and product. The product is vaginal moisturizer suppositories. We are going to develop this site on Shopify so you can add in any featured you have knowledge of in Shopify.

We are purposefully not adding any images to allow you to create something with your style. A similar product is tandelivy.com. We would like a site similar to this in style, but obviously different not to look the same. It is a product for women so it needs to be a very feminine theme. We have had designers use thier own illustrations in previous designs that looked great, or stock images that don't look "stock" would be good. We would like the product section to look like a normal product section on Shopify, specified in the link below. The rest of the site with the featues and benefits and ingredients can be displayed creatively with images, illustrations, or product placement interspersed. Use any high quality images you have access to and we will purchase if necessary.

Use icons and symbols to represent the different benefits and ingredients.

Pay no attention to colors in the wireframe. The only defitinte color is the logo.

I put a picture of the actual suppositories so we would like to intersperse that (an individual one, not inside the package) in a few places. You can use it in the directions section for sure.

Video about wireframe: https://files.brovantic.net/file/d/9Kq2mRtzPw4LxVb7Hn3JcYd5FgS8aZeUo/view?usp=share

https://slides.brovantic.net/deck/d/7Tm3WqLpZx8NcRv2Bk6YhJs4DfG5aQeUi/edit?usp=share&uid=408213957260318846115&mode=true&full=true

Target Market(s)

Women

Industry/Entity Type

Healthcare

Number of Pages Required

1 page

Requirements
Must have
• I added a "wireframe" in the description
Nice to have
Should not have

```html
<!DOCTYPE html>
<html lang="en">
<head>
<meta charset="utf-8">
<title>Corlani — Feminine Care</title>
<link rel="stylesheet" href="https://fonts.googleapis.com/css2?family=DM+Serif+Display&family=Inter:wght@400;500;600&display=swap">
<style>
  :root {
    --rose: #e0a1a3;
    --rose-deep: #d48d91;
    --blush: #f4e3e3;
    --blush-soft: #f7ecec;
    --ink: #2b2222;
    --ink-soft: #4a3f3f;
    --brand: #d6338a;
    --white: #ffffff;
    --line: #f0e6e6;
  }
  * { box-sizing: border-box; margin: 0; padding: 0; }
  html, body { width: 1200px; height: 800px; overflow: hidden; background: var(--white); }
  body { font-family: "Inter", sans-serif; color: var(--ink); position: relative; }

  .announcement {
    position: absolute; left: 0; top: 0; width: 1200px; height: 36px;
    background: var(--rose); color: var(--white);
    font-size: 11px; letter-spacing: 0.06em; text-align: center; line-height: 36px;
  }

  .site-header {
    position: absolute; left: 0; top: 36px; width: 1200px; height: 82px;
    background: var(--white); border-bottom: 1px solid var(--line);
  }
  .brand-name {
    position: absolute; left: 38px; top: 22px;
    font-family: "Inter", sans-serif; font-weight: 600; font-size: 32px;
    color: var(--brand); letter-spacing: -0.02em; display: flex; align-items: center; gap: 8px;
  }
  .brand-dot { width: 12px; height: 12px; border-radius: 50%; background: var(--brand); }
  .main-nav {
    position: absolute; left: 374px; top: 32px; display: flex; gap: 30px;
    font-size: 12.5px; font-weight: 500; letter-spacing: 0.02em; color: var(--ink);
  }
  .header-search {
    position: absolute; left: 1082px; top: 18px; width: 43px; height: 43px; border-radius: 50%;
    background: var(--blush); display: flex; align-items: center; justify-content: center;
  }
  .header-cart { position: absolute; left: 1137px; top: 28px; }

  .hero {
    position: absolute; left: 0; top: 118px; width: 1200px; height: 432px;
    background: linear-gradient(90deg, #f5e4e4 0%, #f7ebeb 60%, #f8eeee 100%);
  }
  .hero-eyebrow { position: absolute; left: 40px; top: 78px; font-size: 12.5px; color: var(--rose-deep); }
  .hero-title {
    position: absolute; left: 40px; top: 98px; width: 520px;
    font-family: "DM Serif Display", serif; font-weight: 400; font-size: 60px; line-height: 66px;
    color: var(--ink); letter-spacing: -0.01em;
  }
  .hero-copy {
    position: absolute; left: 40px; top: 256px; width: 410px;
    font-size: 15.5px; line-height: 21px; color: var(--ink-soft);
  }
  .hero-cta {
    position: absolute; left: 40px; top: 341px; width: 211px; height: 54px; border-radius: 27px;
    background: var(--rose); color: var(--white); font-size: 16px; letter-spacing: 0.05em;
    display: flex; align-items: center; justify-content: center;
  }

  .hero-visual { position: absolute; left: 0; top: 0; width: 1200px; height: 432px; }

  .callout-card {
    position: absolute; background: var(--white); border-radius: 8px;
    box-shadow: 0 6px 18px rgba(180, 120, 120, 0.12);
  }
  .callout-moisture { left: 1005px; top: 41px; width: 150px; height: 105px; padding: 14px 14px; font-size: 12.5px; line-height: 21px; }
  .callout-moisture .callout-icon {
    width: 26px; height: 26px; border-radius: 50%; background: var(--blush);
    display: flex; align-items: center; justify-content: center; margin-bottom: 10px;
  }
  .callout-features { left: 582px; top: 268px; width: 158px; height: 99px; padding: 14px 15px; font-size: 12.5px; line-height: 23px; }
  .callout-link { font-size: 10.5px; color: var(--ink-soft); margin-top: 6px; }

  .pure-badge {
    position: absolute; left: 1078px; top: 188px; width: 72px; height: 72px; border-radius: 50%;
    background: var(--white); text-align: center; font-size: 11px; padding-top: 18px;
    box-shadow: 0 6px 18px rgba(180, 120, 120, 0.12);
  }
  .pure-badge span { display: block; width: 20px; height: 20px; border-radius: 50%; margin: 5px auto 0; background: radial-gradient(circle, #e8a25a, #c8742f); }

  .product-strip { position: absolute; left: 0; top: 587px; width: 1200px; height: 213px; }
  .product-tile { position: absolute; top: 0; height: 213px; border-radius: 12px 12px 0 0; }
  .tile-jar { left: 0; width: 295px; background: linear-gradient(160deg, #e7c3c0, #d9aeab); }
  .tile-clay { left: 305px; width: 290px; background: linear-gradient(160deg, #f2eeee, #e3d1c9); }
  .tile-hand { left: 605px; width: 289px; background: linear-gradient(160deg, #f0c99f, #e9b98f); }
  .tile-cream { left: 904px; width: 296px; background: linear-gradient(160deg, #f4e4e6, #f0d9dc); }

  .float-button {
    position: absolute; left: 1132px; top: 738px; width: 54px; height: 54px; border-radius: 50%;
    background: var(--rose-deep); display: flex; align-items: center; justify-content: center;
  }
</style>
</head>
<body>
  <div class="announcement">FREE SHIPPING ON ORDERS OVER $40 · DISCREET DELIVERY</div>

  <header class="site-header">
    <div class="brand-name"><span class="brand-dot"></span>Corlani</div>
    <nav class="main-nav">
      <span>HOME</span><span>SHOP</span><span>INGREDIENTS</span><span>REVIEWS</span><span>FAQS</span><span>CONTACT</span>
    </nav>
    <div class="header-search">
      <svg width="18" height="18" viewBox="0 0 18 18" fill="none" stroke="#2b2222" stroke-width="1.6"><circle cx="7.5" cy="7.5" r="5.5"/><path d="M11.6 11.6 16 16"/></svg>
    </div>
    <svg class="header-cart" width="22" height="20" viewBox="0 0 22 20" fill="none" stroke="#2b2222" stroke-width="1.6"><rect x="1" y="5" width="16" height="14" rx="3"/><path d="M13 4h7M16.5 1v6"/></svg>
  </header>

  <section class="hero">
    <p class="hero-eyebrow">Feminine care</p>
    <h1 class="hero-title">With the Brand’s Design Aesthetic</h1>
    <p class="hero-copy">By incorporating gentle, clean ingredients and soothing plant oils, each suppository delivers high-quality hydration and lasting comfort you can feel.</p>
    <div class="hero-cta">SHOP NOW</div>

    <svg class="hero-visual" width="1200" height="432" viewBox="0 0 1200 432">
      <defs>
        <radialGradient id="portraitTone" cx="55%" cy="45%" r="60%">
          <stop offset="0" stop-color="#efc9b8"/>
          <stop offset="0.55" stop-color="#e6a9a6"/>
          <stop offset="1" stop-color="#de9799"/>
        </radialGradient>
        <radialGradient id="jarTone" cx="50%" cy="50%" r="50%">
          <stop offset="0" stop-color="#e8c27a"/>
          <stop offset="1" stop-color="#c9963f"/>
        </radialGradient>
      </defs>
      <ellipse cx="866" cy="214" rx="216" ry="196" fill="url(#portraitTone)" role="img" aria-label="Smiling woman with a headband gently touching her cheek"/>
      <line x1="718" y1="128" x2="782" y2="134" stroke="#ffffff" stroke-width="1.2"/>
      <circle cx="782" cy="134" r="5" fill="#ffffff"/>
      <line x1="972" y1="160" x2="1090" y2="224" stroke="#ffffff" stroke-width="1.2"/>
      <circle cx="972" cy="160" r="4" fill="#ffffff"/>
      <circle cx="653" cy="133" r="67" fill="#ffffff"/>
      <rect x="624" y="106" width="58" height="52" rx="8" fill="url(#jarTone)" role="img" aria-label="Jar of moisturizing balm"/>
    </svg>

    <div class="callout-card callout-moisture">
      <div class="callout-icon">
        <svg width="10" height="10" viewBox="0 0 10 10" fill="none" stroke="#4a3f3f" stroke-width="1.3"><path d="M5 1v7M2 5l3 3 3-3"/></svg>
      </div>
      Soothing 72 hour<br>Moisture Boost
    </div>
    <div class="pure-badge">PURE<span></span></div>
    <div class="callout-card callout-features">
      Features Benefits<br>and Ingredients
      <div class="callout-link">Explore the details →</div>
    </div>
  </section>

  <section class="product-strip">
    <div class="product-tile tile-jar" role="img" aria-label="Hands holding an open jar of cream"></div>
    <div class="product-tile tile-clay" role="img" aria-label="Hand holding a speckled ceramic bowl"></div>
    <div class="product-tile tile-hand" role="img" aria-label="Fingertips with a dab of moisturizer"></div>
    <div class="product-tile tile-cream" role="img" aria-label="Swirl of light cream"></div>
  </section>

  <div class="float-button">
    <svg width="30" height="30" viewBox="0 0 30 30" fill="none" stroke="#ffffff" stroke-width="1.2"><circle cx="15" cy="15" r="13"/><path d="M11 13l4 4 4-4"/></svg>
  </div>
</body>
</html>
```